New Coffee Shop business card

We are opening our new coffee shop and are needing business cards to take with us on February 6th to Atlanta, Ga to a show.

We will be offering the following menu type items:

coffee
teas
espresso
frappes
smoothies

sandwiches
soups
salads
pastries
ice cream

Our shop is in a rural country-side area and we would like to convey that feel in our shop. In addition to the cafe we will also be selling gifts and furniture and other home decor. Much of this merchandise will be rescued, refurbished or repurposed which is also a core value of what we are all about.

We have a company logo we would like incorporated into the design.

We will also provide files that have the elements of the logo which may also be useful in the design of the card.

Since we are not open yet we need one slightly altered version of the card as well as the final product which states "Opening in the summer 2015"

Target Market(s)

moderate to slightly upscale and folksy.

Industry/Entity Type

Coffee Shop

Contact Information for Business Card

Fern Kettle Coffee
name
address
phone number
email

Card

Font styles to use
Sans Serif

Requirements
Must have
• Must include Logo
• Must include information on menu.
• Must include information on our merchandise sales as described inthe project description.
• Color scheme to complement the logo
Nice to have
• The following descriptions
• "We are also selling gifts, furniture, and other home decoration."
• "We rescue, refurbish, and repurpose old furniture so it can live again."

```html
<!DOCTYPE html>
<html lang="en">
<head>
<meta charset="utf-8">
<title>Fern Kettle Coffee – Business Cards</title>
<link rel="stylesheet" href="https://fonts.googleapis.com/css2?family=Libre+Baskerville&family=Questrial&display=swap">
<style>
  :root {
    --page-bg: #d9d9d7;
    --front-bg: #231f20;
    --gold: #d9a53a;
    --cream: #ecd6a6;
    --cream-deep: #b8925a;
    --back-top: #261f1b;
    --back-bottom: #7b5b2c;
    --back-text: #f3ece0;
  }
  * { margin: 0; padding: 0; box-sizing: border-box; }
  html, body {
    width: 1200px; height: 1000px; overflow: hidden;
    background: var(--page-bg);
  }
  .sheet { position: relative; width: 1200px; height: 1000px; }

  .card {
    position: absolute; left: 250px; width: 700px; height: 400px;
    overflow: hidden; box-shadow: 0 6px 18px rgba(0,0,0,.25);
  }

  /* Front */
  .card--front { top: 60px; background: var(--front-bg); }
  .front__ornament { position: absolute; left: 0; top: 0; width: 440px; height: 250px; }
  .front__brand {
    position: absolute; right: 44px; top: 58px;
    display: flex; align-items: center; gap: 10px;
    font-family: "Libre Baskerville", serif; font-size: 17px; color: var(--gold);
  }
  .front__brand-dot { width: 12px; height: 12px; border-radius: 50%; background: var(--gold); }
  .front__contact {
    position: absolute; right: 44px; bottom: 44px; text-align: right;
    font-family: "Libre Baskerville", serif; font-style: normal;
    font-size: 17px; line-height: 1.55; color: var(--gold);
  }
  .front__name { font-size: 18px; }

  /* Back */
  .card--back {
    top: 540px;
    background: linear-gradient(180deg, var(--back-top) 0%, #3d3023 45%, var(--back-bottom) 100%);
    color: var(--back-text);
    font-family: "Questrial", sans-serif;
  }
  .back__content {
    position: absolute; left: 40px; top: 30px; width: 400px; text-align: center;
    font-size: 17px; line-height: 1.3;
  }
  .menu__title { margin-bottom: 2px; }
  .menu__columns {
    display: flex; justify-content: center; gap: 60px; margin-bottom: 16px;
  }
  .menu__list { list-style: none; text-align: center; width: 110px; }
  .menu__list--food { padding-top: 22px; }
  .back__note { margin-bottom: 16px; }
  .back__cup { position: absolute; right: 40px; top: 60px; width: 200px; height: 310px; }
  .back__brand {
    position: absolute; right: 62px; bottom: 58px;
    display: flex; align-items: center; gap: 8px;
    font-size: 16px; color: var(--back-text);
  }
  .back__brand-dot { width: 10px; height: 10px; background: var(--back-text); }
</style>
</head>
<body>
<main class="sheet">

  <section class="card card--front">
    <svg class="front__ornament" viewBox="0 0 440 250" role="img" aria-label="Cream scrolling flourish ornament sweeping across the top left">
      <defs>
        <linearGradient id="ornamentTone" x1="0" y1="1" x2="1" y2="0">
          <stop offset="0" stop-color="#ecd6a6"/>
          <stop offset="1" stop-color="#b8925a"/>
        </linearGradient>
      </defs>
      <path d="M0 250 C60 170 150 110 260 70 C330 45 400 30 440 28 L440 70 C380 70 320 85 250 110 C150 150 80 200 30 250 Z" fill="url(#ornamentTone)" opacity="0.9"/>
    </svg>

    <div class="front__brand">
      <span class="front__brand-dot"></span>
      <span class="front__brand-name">Fern Kettle Coffee</span>
    </div>

    <address class="front__contact">
      <div class="front__name">Your Name Your Name</div>
      <div>Address, Country, State, Zip 000000</div>
      <div>000 0000 0000</div>
      <div>your_email@company.com</div>
    </address>
  </section>

  <section class="card card--back">
    <div class="back__content">
      <p class="menu__title">Menu:</p>
      <div class="menu__columns">
        <ul class="menu__list menu__list--drinks">
          <li>Coffee</li><li>Teas</li><li>Espresso</li><li>Frappes</li><li>Smoothies</li>
        </ul>
        <ul class="menu__list menu__list--food">
          <li>Sandwiches</li><li>Soups</li><li>Salads</li><li>Pastries</li><li>Ice cream</li>
        </ul>
      </div>
      <p class="back__note">Opening in the summer 2015.</p>
      <p class="back__note">We are also selling gifts, furniture, and other<br>home decoration.</p>
      <p class="back__note">We rescue, refurbish, and repurpose old<br>furniture so it can live again.</p>
    </div>

    <svg class="back__cup" viewBox="0 0 200 310" role="img" aria-label="Faint illustration of a steaming coffee cup">
      <defs>
        <linearGradient id="cupTone" x1="0" y1="0" x2="0" y2="1">
          <stop offset="0" stop-color="#4a3a2c" stop-opacity="0.35"/>
          <stop offset="1" stop-color="#3a2d22" stop-opacity="0.85"/>
        </linearGradient>
      </defs>
      <rect x="0" y="0" width="200" height="310" rx="16" fill="url(#cupTone)"/>
    </svg>

    <div class="back__brand">
      <span class="back__brand-dot"></span>
      <span>Fern Kettle Coffee</span>
    </div>
  </section>

</main>
</body>
</html>
```